Human Resource Consulting practice needs a business card design

We need a business card design (double sided colour) for our Human Resource (HR) consulting practice in regional New South Wales, australia. Our business name is Staff Compass. We support small and medium business across the Mid North Coast of New South Wales by providing them with outsourced HR support, services and products to help them achieve compliance with workplace legislation and across all areas of the employment lifecycle from recruitment to termination and everything in between. Our corporate colours are hot pink and black. The final design should communicate professionalism, trust, people focus.
I have attached the current (old) business card for your reference.

Target Market(s)

Business owners and high level managers

Industry/Entity Type

Business

Contact Information for Business Card

Name
Title
Phone no
Mobile no
Address
PO Box
email address
website

Colors
e34197

Requirements
Must have
• Tempate for changing business card personal details including Name, position title, mobile number, email address.
• Keep current logo and colours as per attached
• Logo must be presented in 2 colours or black only not white
Nice to have
• One side logo and graphic only other side logo and personal details
Should not have
• Should not be the same as the current version (attached) but a modern interpretation.
• Does not need a busy reverse side with our list of services as per current version. I feel this is too busy.
• No photos

```html
<!DOCTYPE html>
<html lang="en">
<head>
<meta charset="utf-8">
<title>Staff Compass – Business Card</title>
<link rel="stylesheet" href="https://fonts.googleapis.com/css2?family=Michroma&display=swap">
<style>
  :root {
    --stage: #3b3b3d;
    --card: #2b2929;
    --pink: #e3168f;
    --white: #ffffff;
    --rule: #8a8888;
  }
  * { box-sizing: border-box; margin: 0; padding: 0; }
  html, body { width: 1200px; height: 1189px; overflow: hidden; }
  body {
    background: var(--stage);
    font-family: "Michroma", "Arial", sans-serif;
    color: var(--white);
    position: relative;
  }
  .card {
    position: absolute;
    left: 170px;
    width: 860px;
    height: 491px;
    background: var(--card);
    border-radius: 28px;
    box-shadow: 0 14px 30px rgba(0,0,0,.45);
    overflow: hidden;
  }
  .card--front { top: 70px; }
  .card--back { top: 626px; }

  /* Logo side */
  .brand {
    position: absolute;
    display: flex;
    align-items: center;
    gap: 18px;
    font-size: 52px;
    letter-spacing: 1px;
    white-space: nowrap;
  }
  .brand__mark {
    width: 22px; height: 22px;
    background: currentColor;
    flex: none;
  }
  .card--front .brand {
    color: var(--white);
    left: 50%; top: 170px;
    transform: translateX(-50%);
  }
  .web-line {
    position: absolute;
    left: 150px; right: 150px; top: 330px;
    display: flex; align-items: center; gap: 22px;
    font-size: 17px; letter-spacing: 2px;
    white-space: nowrap;
  }
  .web-line::before, .web-line::after {
    content: ""; flex: 1; height: 1px; background: var(--rule);
  }

  /* Details side */
  .card--back .brand {
    color: var(--pink);
    left: 60px; top: 110px;
    font-size: 33px;
    gap: 14px;
  }
  .card--back .brand__mark { width: 18px; height: 18px; }
  .person {
    position: absolute;
    right: 60px; top: 92px;
    text-align: right;
    white-space: nowrap;
  }
  .person__name {
    color: var(--pink);
    font-size: 24px;
    letter-spacing: 1px;
    -webkit-text-stroke: .6px var(--pink);
  }
  .person__title {
    font-size: 14px;
    letter-spacing: 1.2px;
    margin-top: 8px;
  }
  .divider {
    position: absolute;
    left: 60px; right: 60px; top: 215px;
    height: 1px; background: var(--rule);
  }
  .contacts {
    position: absolute;
    left: 60px; top: 285px;
    list-style: none;
  }
  .contacts li {
    display: flex; align-items: center; gap: 20px;
    font-size: 20px; letter-spacing: 1.5px;
    height: 42px;
    white-space: nowrap;
  }
  .contacts svg { width: 30px; height: 30px; flex: none; }
  .address {
    position: absolute;
    right: 60px; top: 260px;
    text-align: right;
    font-size: 20px; letter-spacing: 1.5px; line-height: 1.7;
    white-space: nowrap;
  }
</style>
</head>
<body>

<section class="card card--front" aria-label="Card front">
  <div class="brand"><span class="brand__mark"></span>Staff Compass</div>
  <p class="web-line">www.staffcompass.com.au</p>
</section>

<section class="card card--back" aria-label="Card back">
  <div class="brand"><span class="brand__mark"></span>Staff Compass</div>

  <div class="person">
    <p class="person__name">Megan Harlow</p>
    <p class="person__title">PRINCIPAL CONSULTANT</p>
  </div>

  <div class="divider"></div>

  <ul class="contacts">
    <li>
      <svg viewBox="0 0 30 30" aria-label="Phone"><rect width="30" height="30" rx="4" fill="var(--pink)"/><path d="M7 12c0-3 3-4 8-4s8 1 8 4l-3 1-1-2c-2-1-6-1-8 0l-1 2zM10 14h10l2 8H8z" fill="#fff"/><circle cx="15" cy="18" r="2" fill="var(--pink)"/></svg>
      02 5550 4183
    </li>
    <li>
      <svg viewBox="0 0 30 30" aria-label="Mobile"><rect width="30" height="30" rx="4" fill="var(--pink)"/><rect x="10" y="5" width="10" height="20" rx="2" fill="#fff"/><rect x="12" y="8" width="6" height="7" fill="var(--pink)"/></svg>
      0400 555 118
    </li>
    <li>
      <svg viewBox="0 0 30 30" aria-label="Email"><rect width="30" height="30" rx="4" fill="var(--pink)"/><rect x="5" y="9" width="20" height="13" fill="#fff"/><path d="M5 9l10 8 10-8" fill="none" stroke="var(--pink)" stroke-width="1.5"/></svg>
      megan@staffcompass.com.au
    </li>
    <li>
      <svg viewBox="0 0 30 30" aria-label="Website"><rect width="30" height="30" rx="4" fill="var(--pink)"/><circle cx="15" cy="15" r="9" fill="none" stroke="#fff" stroke-width="2"/><ellipse cx="15" cy="15" rx="4" ry="9" fill="none" stroke="#fff" stroke-width="1.5"/><path d="M6 15h18" stroke="#fff" stroke-width="1.5"/></svg>
      www.staffcompass.com.au
    </li>
  </ul>

  <p class="address">P.O. Box 210<br>Harbourton, NSW 2400</p>
</section>

</body>
</html>
```